RTavenor Business Cards & Letterhead

I have a logo but need a design for some new business cards. We are a Design-Build Firm that specializes in the design and construction of commercial projects.
the cards need to be professional. no cartoon stuff.
i would like to have the cards in AI format so I can update the card as needed. Logo is provided.
Our Address is: 4187 Marlowe Ct. Cedar Bluff, Vermont 27614

```html
<!DOCTYPE html>
<html lang="en">
<head>
<meta charset="utf-8">
<title>RTavenor Business Card</title>
<link rel="stylesheet" href="https://fonts.googleapis.com/css2?family=Open+Sans:wght@400;600;800&display=swap">
<style>
  :root {
    --page: #1d1d20;
    --card-dark: #222226;
    --blue: #1479bd;
    --blue-deep: #0c4e82;
    --blue-bright: #1a8ad4;
    --grey: #8a8a8e;
    --white: #f2f2f2;
  }
  html, body {
    margin: 0;
    padding: 0;
    width: 1200px;
    height: 780px;
    overflow: hidden;
    background: var(--page);
    font-family: "Open Sans", Arial, sans-serif;
  }
  .canvas {
    position: relative;
    width: 1200px;
    height: 780px;
  }
  .card {
    position: absolute;
    top: 235px;
    width: 530px;
    height: 310px;
    border-radius: 22px;
    overflow: hidden;
  }
  .card-front {
    left: 45px;
    background: radial-gradient(ellipse at 55% 50%, var(--blue) 0%, #0f5e98 45%, var(--blue-deep) 100%);
  }
  .front-wordmark {
    position: absolute;
    left: 0;
    right: 0;
    top: 50%;
    transform: translateY(-50%);
    text-align: center;
    font-weight: 800;
    font-size: 62px;
    letter-spacing: 2px;
    color: #0b4675;
  }
  .card-back {
    left: 625px;
    background: var(--card-dark);
  }
  .back-shapes {
    position: absolute;
    inset: 0;
  }
  .holder {
    position: absolute;
    right: 34px;
    top: 30px;
    text-align: right;
  }
  .holder-name {
    margin: 0;
    font-weight: 800;
    font-size: 22px;
    letter-spacing: 1px;
    color: var(--blue-bright);
  }
  .holder-title {
    margin: 2px 0 0;
    font-weight: 600;
    font-size: 14px;
    color: var(--white);
  }
  .back-wordmark {
    position: absolute;
    left: 34px;
    top: 92px;
    display: flex;
    align-items: center;
    gap: 8px;
    font-weight: 800;
    font-size: 32px;
    letter-spacing: 1px;
    color: var(--grey);
  }
  .back-wordmark .mark-square {
    width: 20px;
    height: 20px;
    background: var(--blue);
  }
  .contact {
    position: absolute;
    left: 62px;
    top: 148px;
    color: var(--white);
    font-size: 14.5px;
    line-height: 1.35;
  }
  .contact p { margin: 0; }
  .contact .address { margin-bottom: 12px; }
  .contact-line {
    display: flex;
    align-items: center;
    gap: 8px;
  }
  .contact-line svg { flex: none; }
</style>
</head>
<body>
<main class="canvas">
  <section class="card card-front" aria-label="Card front">
    <div class="front-wordmark">RTAVENOR</div>
  </section>

  <section class="card card-back" aria-label="Card back">
    <svg class="back-shapes" width="530" height="310" viewBox="0 0 530 310" aria-hidden="true">
      <defs>
        <linearGradient id="backWave" x1="0" y1="1" x2="1" y2="0">
          <stop offset="0" stop-color="#0d5a94"/>
          <stop offset="0.5" stop-color="#1a82c8"/>
          <stop offset="1" stop-color="#0c4e82"/>
        </linearGradient>
      </defs>
      <path d="M170 310 C 290 300 365 235 388 140 C 402 95 460 88 530 80 L530 310 Z" fill="url(#backWave)"/>
      <path d="M140 292 C 240 300 330 268 372 205 C 340 275 250 306 155 308 Z" fill="var(--grey)"/>
      <rect x="505" y="26" width="25" height="50" fill="var(--blue)"/>
    </svg>

    <div class="holder">
      <p class="holder-name">MARCUS TAVENOR</p>
      <p class="holder-title">Founder/President</p>
    </div>

    <div class="back-wordmark"><span class="mark-square"></span>RTAVENOR</div>

    <div class="contact">
      <p class="address">4187 Marlowe Ct. Cedar Bluff,<br>Vermont 27614</p>
      <p class="contact-line">
        <svg width="12" height="12" viewBox="0 0 12 12" aria-hidden="true"><circle cx="6" cy="6" r="6" fill="var(--blue)"/><path d="M4 3 L5 3 L5.6 4.6 L4.9 5.2 Q5.6 6.6 6.8 7.1 L7.4 6.4 L9 7 L9 8 Q8.8 9 7.6 9 Q4 8.4 3 4.4 Q3 3.2 4 3 Z" fill="var(--white)"/></svg>
        (802) 555-0148
      </p>
      <p class="contact-line">
        <svg width="12" height="12" viewBox="0 0 12 12" aria-hidden="true"><circle cx="6" cy="6" r="6" fill="var(--blue)"/><circle cx="6" cy="6" r="3.3" fill="none" stroke="var(--white)" stroke-width="0.8"/><path d="M2.7 6 H9.3 M6 2.7 V9.3" stroke="var(--white)" stroke-width="0.8"/></svg>
        www.rtavenor.com
      </p>
      <p class="contact-line">
        <svg width="12" height="12" viewBox="0 0 12 12" aria-hidden="true"><circle cx="6" cy="6" r="6" fill="var(--blue)"/><rect x="3" y="4" width="6" height="4.2" fill="none" stroke="var(--white)" stroke-width="0.8"/><path d="M3 4 L6 6.4 L9 4" fill="none" stroke="var(--white)" stroke-width="0.8"/></svg>
        MRT@RTavenor.com
      </p>
    </div>
  </section>
</main>
</body>
</html>
```